Business Card Design

We need a design for business cards for our company. We have a logo. We teach EMT's and we are based out of Virginia. The information that will need to add would be, name, title, phone number, email, address. On the back of the business card would be "We help you, help others"

Target Market(s)

People that want to become EMT's

Colors

Designer to choose colors to be used in the design.

Requirements
Must have
• company logo

```html
<!DOCTYPE html>
<html lang="en">
<head>
<meta charset="utf-8">
<title>Medic Path Academy – Business Cards</title>
<link href="https://fonts.googleapis.com/css2?family=Montserrat:wght@400;500;600&display=swap" rel="stylesheet">
<style>
  :root{
    --backdrop:#e9e7e5;
    --card-dark:#1f2a35;
    --card-light:#ffffff;
    --brand-red:#c0202f;
    --text-grey:#8a8c91;
    --swoosh-grey:#a7a9ad;
  }
  *{box-sizing:border-box;margin:0;padding:0}
  html,body{width:1200px;height:912px;overflow:hidden}
  body{
    background:var(--backdrop);
    font-family:"Montserrat",sans-serif;
    position:relative;
  }
  .card{
    position:absolute;
    left:320px;
    width:560px;height:320px;
    border-radius:2px;
    box-shadow:0 8px 24px rgba(0,0,0,.18);
    overflow:hidden;
  }
  .card--back{top:100px;background:var(--card-dark)}
  .card--front{top:492px;background:var(--card-light)}

  .brand{
    position:absolute;
    display:flex;align-items:center;gap:8px;
    font-weight:600;
    color:var(--brand-red);
    white-space:nowrap;
  }
  .brand__dot{
    width:12px;height:12px;border-radius:50%;
    background:var(--brand-red);flex:none;
  }
  .card--back .brand{left:50%;top:50%;transform:translate(-50%,-50%);font-size:30px;gap:10px}
  .card--back .brand__dot{width:14px;height:14px}
  .card--front .brand{left:34px;top:146px;font-size:18px}

  .divider{
    position:absolute;left:272px;top:40px;
    width:1.5px;height:150px;background:var(--brand-red);
  }
  .contact{
    position:absolute;left:292px;top:30px;
    color:var(--text-grey);font-size:12px;line-height:1.4;
    white-space:nowrap;
  }
  .contact__name{
    color:var(--brand-red);font-size:20px;font-weight:600;
    letter-spacing:.3px;line-height:1.1;
  }
  .contact__title{font-size:12.5px;margin-bottom:8px}
  .contact__address{margin-bottom:6px}
  .contact__row{display:flex;align-items:center;gap:8px}
  .contact__row svg{width:11px;height:11px;flex:none}
  .swoosh{position:absolute;left:0;top:0;width:560px;height:320px}
</style>
</head>
<body>

  <section class="card card--back" aria-label="Card back">
    <div class="brand"><span class="brand__dot"></span>Medic Path Academy</div>
  </section>

  <section class="card card--front" aria-label="Card front">
    <svg class="swoosh" viewBox="0 0 560 320" aria-hidden="true">
      <path d="M170 320 C320 255 450 222 560 205 L560 214 C450 232 330 265 200 320 Z" fill="var(--swoosh-grey)"/>
      <path d="M225 320 C350 268 460 238 560 222 L560 320 Z" fill="var(--brand-red)"/>
    </svg>

    <div class="brand"><span class="brand__dot"></span>Medic Path Academy</div>

    <div class="divider"></div>

    <div class="contact">
      <p class="contact__name">DANIEL REYES</p>
      <p class="contact__title">Director</p>
      <p class="contact__address">418 Harbor Ave.<br>Lakewood, VA 23150</p>
      <p class="contact__row">
        <svg viewBox="0 0 12 12"><path d="M3 1l2 2-1 1.5c.7 1.4 1.6 2.3 3 3L8.5 6.5l2 2-1.3 1.8C5.5 10 2 6.5 1.7 2.3z" fill="var(--brand-red)"/></svg>
        555-204-7316
      </p>
      <p class="contact__row">
        <svg viewBox="0 0 12 12"><rect x="1" y="2.5" width="10" height="7" fill="none" stroke="var(--brand-red)" stroke-width="1.2"/><path d="M1 2.5l5 4 5-4" fill="none" stroke="var(--brand-red)" stroke-width="1.2"/></svg>
        hello@medicpathacademy.com
      </p>
      <p class="contact__row">
        <svg viewBox="0 0 12 12"><circle cx="6" cy="6" r="5" fill="none" stroke="var(--brand-red)" stroke-width="1.2"/><path d="M1 6h10M6 1c-2.5 3-2.5 7 0 10M6 1c2.5 3 2.5 7 0 10" fill="none" stroke="var(--brand-red)" stroke-width="1"/></svg>
        www.medicpathacademy.com
      </p>
    </div>
  </section>

</body>
</html>
```